U.S. Popcorn company needs business cards

We are a popcorn company that manufactures popcorn and sells it to grocery stores worldwide. Our theme is "Americana" and our logo is U.S. route 66 which is the most famous highway in the U.S.

We would like the design to be simple and to use both sides. On the back side we would like to see just the logo and website. The front would be normal details

Target Market(s)

Wholesalers, grocers and distributors

Industry/Entity Type

Manufacture

Contact Information for Business Card

Business name: Prairie Lantern Popcorn
Phone: +1 555 308 4726
Email: Dale@prairielanternpopcorn.com
website: www.prairielanternpopcorn.com
Tag Line: "POPped fresh, sold proud"
Name: Dale Whitcombe
Title: Founder/President

Requirements
Must have
• Either this design should be fun or clean and simple. I will let you show me your thougths.
Nice to have
• Anything that ties in the real Hwy Route 66.
• Colors might need to be red, white and blue incorporated.
Should not have
• Not be too busy.

```html
<!DOCTYPE html>
<html lang="en">
<head>
<meta charset="utf-8">
<title>Prairie Lantern Popcorn – Business Cards</title>
<link rel="stylesheet" href="https://fonts.googleapis.com/css2?family=Mulish:wght@400;700;800&display=swap">
<style>
  :root {
    --navy: #11306a;
    --red: #d9262b;
    --white: #f4f5f6;
    --paper: #e6e7e8;
    --text-light: #ffffff;
  }
  * { box-sizing: border-box; margin: 0; padding: 0; }
  html, body { width: 1200px; height: 576px; overflow: hidden; }
  body {
    background: var(--paper);
    font-family: "Mulish", sans-serif;
    position: relative;
  }
  .card {
    position: absolute;
    width: 484px;
    height: 293px;
    border-radius: 6px;
    overflow: hidden;
    background: var(--navy);
  }
  .card--back { left: 82px; top: 139px; }
  .card--front { left: 602px; top: 138px; width: 481px; height: 291px; }

  /* shared brand name */
  .brand-name {
    position: absolute;
    left: 0; right: 0;
    text-align: center;
    font-weight: 800;
    text-transform: uppercase;
    line-height: 1.05;
    letter-spacing: 0.5px;
  }

  /* back side */
  .card--back .brand-name {
    top: 100px;
    font-size: 34px;
    color: var(--text-light);
  }
  .brand-mark {
    position: absolute;
    left: 50%;
    top: 72px;
    width: 16px; height: 16px;
    margin-left: -8px;
    border-radius: 50%;
    background: var(--red);
  }
  .website-row {
    position: absolute;
    left: 0; right: 0; bottom: 22px;
    display: flex;
    align-items: center;
    justify-content: center;
    gap: 10px;
    color: var(--text-light);
    font-size: 11.5px;
    font-weight: 700;
    letter-spacing: 0.2px;
  }
  .website-row .rule {
    width: 42px; height: 2px;
    background: var(--red);
  }

  /* front side */
  .front-shape { position: absolute; inset: 0; }
  .holder {
    position: absolute;
    left: 21px; top: 34px;
    color: var(--text-light);
  }
  .holder-name { font-size: 22px; font-weight: 700; letter-spacing: 0.2px; }
  .holder-title { font-size: 11.5px; font-weight: 400; margin-top: 1px; }
  .card--front .brand-name {
    left: 296px; right: 12px;
    top: 58px;
    font-size: 21px;
    color: var(--navy);
  }
  .contact-list {
    position: absolute;
    left: 22px; top: 216px;
    list-style: none;
    color: var(--text-light);
    font-size: 12.5px;
  }
  .contact-list li {
    display: flex;
    align-items: center;
    gap: 10px;
    height: 17.5px;
  }
  .contact-list svg { width: 12px; height: 12px; fill: var(--text-light); flex: none; }
  .tagline {
    position: absolute;
    right: 21px; top: 245px;
    color: var(--text-light);
    font-size: 15px;
    font-weight: 400;
  }
  .tagline strong { font-weight: 800; }
</style>
</head>
<body>

  <section class="card card--back" aria-label="Back of business card">
    <span class="brand-mark" aria-hidden="true"></span>
    <div class="brand-name">Prairie Lantern<br>Popcorn</div>
    <div class="website-row">
      <span class="rule"></span>
      <span class="website">www.prairielanternpopcorn.com</span>
      <span class="rule"></span>
    </div>
  </section>

  <section class="card card--front" aria-label="Front of business card">
    <svg class="front-shape" viewBox="0 0 481 291" preserveAspectRatio="none" aria-hidden="true">
      <path d="M168,0 C250,0 270,118 322,168 C370,204 430,206 481,208 L481,0 Z" fill="var(--red)"/>
      <path d="M180,0 C262,0 282,112 334,160 C380,196 436,200 481,203 L481,0 Z" fill="var(--white)"/>
    </svg>

    <div class="holder">
      <div class="holder-name">Dale Whitcombe</div>
      <div class="holder-title">Founder/President</div>
    </div>

    <div class="brand-name">Prairie<br>Lantern<br>Popcorn</div>

    <ul class="contact-list">
      <li>
        <svg viewBox="0 0 24 24" aria-hidden="true"><path d="M3 7c0-2 4-4 9-4s9 2 9 4v2h-5V7H8v2H3z M6 11h12l2 9H4z M12 13a3 3 0 1 0 0 6a3 3 0 1 0 0-6z"/></svg>
        <span>+1 555 308 4726</span>
      </li>
      <li>
        <svg viewBox="0 0 24 24" aria-hidden="true"><path d="M2 5h20v14H2z M4 7l8 6l8-6v-.5H4z" fill-rule="evenodd"/></svg>
        <span>Dale@prairielanternpopcorn.com</span>
      </li>
      <li>
        <svg viewBox="0 0 24 24" aria-hidden="true"><path d="M12 2a10 10 0 1 0 0 20a10 10 0 1 0 0-20z M4.2 11h3.8c.1-2.6.7-5 1.6-6.6A8 8 0 0 0 4.2 11z M10 11h4c-.2-3-1-5.6-2-6.9c-1 1.3-1.8 3.9-2 6.9z M16 11h3.8a8 8 0 0 0-5.4-6.6c.9 1.6 1.5 4 1.6 6.6z M4.2 13a8 8 0 0 0 5.4 6.6c-.9-1.6-1.5-4-1.6-6.6z M10 13c.2 3 1 5.6 2 6.9c1-1.3 1.8-3.9 2-6.9z M16 13c-.1 2.6-.7 5-1.6 6.6a8 8 0 0 0 5.4-6.6z" fill-rule="evenodd"/></svg>
        <span>prairielanternpopcorn.com</span>
      </li>
    </ul>

    <p class="tagline">"<strong>POP</strong>ped fresh, sold proud"</p>
  </section>

</body>
</html>
```